Stylish new business card needed!

Hello everyone! I am in need of a new business card design for an alarm company here in Hurricane WV. I have all fonts, color codes and logos provided for you use! We are a young company and like the style of a clean sleek looking business card. Would like it double sided, one side holding the logo and the other with your design!
Target Market(s)
The people that are looking for the newest tech for home automation and security
Industry/Entity Type
Alarm services; Home automation
Contact Information for Business Card
Name of person; position (Sales; Installer); Phone Number (555.418.7260); Employee cell Number; Website (www.GuardedByVelk.example); Employee Email; Double sided
Look and feel
Each slider illustrates characteristics of the customer's brand and the style your logo design should communicate.

```html
<!DOCTYPE html>
<html lang="en">
<head>
<meta charset="utf-8">
<title>Guarded By Velk – Business Card</title>
<link href="https://fonts.googleapis.com/css2?family=Archivo+Black&family=Arimo:wght@400&display=swap" rel="stylesheet">
<style>
  :root {
    --orange: #f48f53;
    --grey: #9b9b9b;
    --ink: #1c1c1c;
    --paper: #ffffff;
    --backdrop: #2b2b2b;
  }
  * { margin: 0; padding: 0; box-sizing: border-box; }
  html, body { width: 1200px; height: 880px; overflow: hidden; }
  body { background: var(--backdrop); position: relative; font-family: "Arimo", Arial, sans-serif; }

  .card {
    position: absolute;
    width: 640px;
    height: 366px;
    overflow: hidden;
    box-shadow: 0 10px 24px rgba(0,0,0,.45);
  }

  /* Brand side */
  .card--brand { left: 190px; top: 52px; background: var(--orange); color: var(--paper); }
  .brand-lockup {
    position: absolute; left: 0; right: 0; top: 78px;
    text-align: center; font-family: "Archivo Black", Arial, sans-serif;
  }
  .brand-lockup__lead { font-size: 26px; letter-spacing: 2px; }
  .brand-lockup__name { font-size: 118px; line-height: 1; letter-spacing: 6px; margin-top: 4px; }
  .brand-tagline {
    position: absolute; left: 0; right: 0; top: 262px;
    text-align: center; font-family: "Archivo Black", Arial, sans-serif;
    font-size: 12px; letter-spacing: 1.5px;
  }

  /* Contact side */
  .card--contact { left: 370px; top: 452px; background: var(--paper); }
  .contact-wave { position: absolute; inset: 0; }
  .contact-logo {
    position: absolute; left: 370px; top: 34px;
    display: flex; align-items: center; gap: 12px;
  }
  .contact-logo__dot { width: 22px; height: 22px; border-radius: 50%; background: var(--orange); }
  .contact-logo__name { font-size: 72px; line-height: 1; color: var(--grey); letter-spacing: 4px; }

  .person { position: absolute; left: 40px; top: 150px; }
  .person__name { font-family: "Archivo Black", Arial, sans-serif; font-size: 24px; letter-spacing: 1.5px; }
  .person__first { color: var(--grey); }
  .person__last { color: var(--orange); }
  .person__role { font-size: 17px; color: var(--ink); margin-top: 2px; }

  .contact-list { position: absolute; left: 40px; top: 232px; list-style: none; }
  .contact-list li {
    display: flex; align-items: center; gap: 10px;
    font-size: 17px; color: var(--ink); line-height: 24px;
  }
  .contact-list svg { width: 15px; height: 15px; fill: var(--orange); flex: none; }
</style>
</head>
<body>

  <section class="card card--brand">
    <div class="brand-lockup">
      <div class="brand-lockup__lead">GUARDED BY</div>
      <div class="brand-lockup__name">VELK</div>
    </div>
    <div class="brand-tagline">AUTOMATION AND SECURITY SERVICES</div>
  </section>

  <section class="card card--contact">
    <svg class="contact-wave" viewBox="0 0 640 366" preserveAspectRatio="none" aria-hidden="true">
      <path d="M80 366 Q 90 336 230 318 Q 470 280 640 160 L640 366 Z" fill="var(--orange)"/>
      <path d="M150 322 Q 430 300 620 180 Q 440 290 150 322 Z" fill="var(--grey)" stroke="var(--grey)" stroke-width="3"/>
    </svg>

    <div class="contact-logo">
      <span class="contact-logo__dot"></span>
      <span class="contact-logo__name">VELK</span>
    </div>

    <div class="person">
      <div class="person__name"><span class="person__first">DALE</span> <span class="person__last">MARLOW</span></div>
      <div class="person__role">Sales; Installer</div>
    </div>

    <ul class="contact-list">
      <li><svg viewBox="0 0 16 16"><path d="M1 5c0-2 2-3 7-3s7 1 7 3v1h-4V5H5v1H1zM3 8l2-2h6l2 2v6H3zm5 1.5a2 2 0 100 4 2 2 0 000-4z"/></svg>555.418.7260</li>
      <li><svg viewBox="0 0 16 16"><path d="M4 1h8v14H4zm1.5 1.5v9h5v-9zM8 12.5a.8.8 0 100 1.6.8.8 0 000-1.6z"/></svg>555.418.7261</li>
      <li><svg viewBox="0 0 16 16"><path d="M1 3h14v10H1zm1.5 1.5L8 9l5.5-4.5z"/></svg>info@GuardedByVelk.example</li>
      <li><svg viewBox="0 0 16 16"><path d="M8 1a7 7 0 110 14A7 7 0 018 1zm-1 2.5C5 4 4 6 4.5 7.5 6 8 6 10 7 11l1 2c3-1 4.5-3 4.5-5-1 0-2-1-2.5-2L9 4z"/></svg>www.GuardedByVelk.example</li>
    </ul>
  </section>

</body>
</html>
```